WordPress Website Design for Multi-Brand Aviation Group (Unified Branding System)

Project Overview:
We are seeking a professional, modern WordPress website design for an aviation-focused umbrella company that owns and operates multiple subsidiary businesses. The goal is to create a cohesive visual system that clearly communicates that each company operates under the same parent organization, while still allowing each brand to maintain a slightly distinct identity.
This is not just a single website design—we are looking for a scalable design framework that can be applied across multiple aviation-related businesses.
Objectives:
- Establish a consistent, recognizable brand identity across all company websites
Clearly communicate the relationship between the parent company and its subsidiaries
-bCreate a clean, high-end corporate aviation aesthetic
- Ensure all designs are SEO-friendly and optimized for performance
- Allow flexibility for future expansion (additional subsidiaries)
- Target Audience:
- Corporate aviation clients
- Charter customers
- Students wishing to receive flight training
- Aircraft owners and operators
- Turbine aircraft training to meet insurance requirements
- Business professionals and high-net-worth individuals
- Aviation industry partners
Design Direction & Style:
We are looking for a premium, professional aviation feel—think clean, modern, and high-trust. The design should reflect the standards of corporate aviation: precision, safety, and sophistication.
Key style notes:
Minimalist but impactful layout
High-quality aviation photography (jets, interiors, operations, global travel)
Subtle motion/interaction (hover effects, transitions)
Clear typography hierarchy for readability and professionalism
Branding Requirements:
Incorporate the primary colors of the parent company logo across all designs
Website Structure (Core Pages):
Design a system that includes:
Home Page with the following links:
- About / Company Overview
- Aircraft Management
- Aircraft Acquisition
- Charter
- Pilot Services
- Trip Support
- Contact Page
Site should further include:
- Mobile-first responsive design
- Fast-loading, performance-optimized layouts
SEO & Technical Considerations:
- Design should support high-level SEO implementation:
- Clean layout structure that translates well to semantic HTML
- Proper heading hierarchy (H1, H2, H3)
- Space for keyword-rich content without clutter
- Optimized image placement (with alt text capability)
- Fast load times (lightweight design approach)
- Compatibility with WordPress SEO plugins (e.g., Yoast or Rank Math)
WordPress Requirements:
- Design should be easily built using WordPress (preferred builders: Elementor, Gutenberg, or similar)
- Reusable templates for scalability across multiple sites
- Easy for non-developers to update text and images
- Modular components (blocks/sections that can be reused across pages and sites)
- Navigation & UX:
- Simple, intuitive navigation
- Sticky header preferred
Style guide including:
- Colors
- Fonts
- Button styles
- Layout system
- Designs similar to high-end corporate aviation, private jet charter, or luxury service brands are preferred—clean, sharp, and premium without being overly flashy.
What We Want to Avoid:
- Overly busy layouts
- Generic templates with no brand identity
- Outdated or “stock” looking aviation designs
- Poor mobile responsiveness
Additional Notes:
We are building a long-term brand system, not just a one-off website. There is potential for ongoing work as we expand additional subsidiary sites.
We value designers who understand branding consistency across multiple business units and can create a scalable, professional system.
Include the attached main company logo "Vireton Aviation Group" and the "Member PJFO" logo on the main page.

```html
<!DOCTYPE html>
<html lang="en">
<head>
<meta charset="utf-8">
<title>Vireton Aviation Group</title>
<link rel="stylesheet" href="https://fonts.googleapis.com/css2?family=Rajdhani:wght@400;500;600;700&family=Michroma&display=swap">
<style>
:root{
  --blue:#0b5eb0;
  --blue-dark:#084c91;
  --ink:#111418;
  --text:#3a3f47;
  --muted:#5c636d;
  --page:#ffffff;
  --soft:#f5f7fa;
  --line:#d7dce3;
  --black:#000000;
  --backdrop:#b4b6b9;
  --white:#ffffff;
}
*{margin:0;padding:0;box-sizing:border-box}
html,body{width:1200px;height:2711px;overflow:hidden;background:var(--backdrop)}
body{font-family:"Rajdhani",sans-serif;color:var(--ink)}
.stage{position:absolute;left:0;top:0;width:1140px;height:2576px;transform:scale(1.052632);transform-origin:0 0}
.site{position:absolute;left:77px;top:77px;width:986px;height:2421px;background:var(--page);overflow:hidden}
a{color:inherit;text-decoration:none}
.eyebrow{font-family:"Michroma",sans-serif;font-size:11px;letter-spacing:2.5px;color:var(--blue);text-transform:uppercase}
.arrow{display:inline-block;width:26px;height:6px;vertical-align:middle;margin-left:4px}

/* header */
.brand{position:absolute;left:48px;top:26px;display:flex;align-items:center;gap:8px}
.brand-mark{width:14px;height:14px;background:var(--blue)}
.brand-name{font-weight:700;font-size:19px;line-height:1;color:var(--blue);letter-spacing:.5px}
.brand-name small{display:block;font-size:19px}
.nav{position:absolute;right:10px;top:12px;display:flex;align-items:center;gap:17px;font-size:8.5px;font-weight:600;color:var(--white)}
.nav .nav-contact{background:var(--blue);padding:4px 7px;border:1px solid #fff3}

/* hero */
.hero{position:absolute;left:0;top:0;width:986px;height:553px;background:linear-gradient(90deg,#e9eef6 0%,#dde6f1 35%,#9eb3cc 55%,#4f6e95 80%,#263f61 100%)}
.hero-photo{position:absolute;left:320px;top:0;width:666px;height:553px;background:radial-gradient(ellipse at 60% 55%,#c9d6e6 0%,#7d97b7 35%,#3a5a82 70%,transparent 100%);opacity:.7}
.hero-curve{position:absolute;left:0;top:0}
.hero-copy{position:absolute;left:48px;top:122px;width:340px}
.hero-copy .kicker{font-family:"Michroma",sans-serif;font-size:11px;letter-spacing:1.5px;color:var(--ink)}
.hero-copy h1{font-size:38px;line-height:42px;font-weight:700;margin-top:6px;letter-spacing:.5px}
.hero-copy p{font-size:14.5px;line-height:19.5px;color:var(--text);margin-top:10px;font-weight:500}
.btns{display:flex;gap:8px;margin-top:14px}
.btn{display:inline-block;font-size:10.5px;font-weight:700;letter-spacing:.4px;padding:5px 10px;border:1px solid var(--blue)}
.btn-solid{background:var(--blue);color:var(--white)}
.btn-line{color:var(--ink);background:#ffffffaa}
.member{margin-top:20px}
.member-badge{display:flex;align-items:center;gap:8px}
.member-badge .dot{width:36px;height:26px;border-radius:50%;background:var(--blue)}
.member-badge span{font-size:24px;font-weight:500;color:var(--ink);letter-spacing:3px;line-height:1}
.member-badge em{position:absolute;margin:-30px 0 0 44px;font-style:normal;font-size:9px;color:var(--text)}
.member .line1{font-size:9.5px;font-weight:600;margin-top:6px}
.member .line2{font-size:7.5px;color:var(--text);margin-top:2px}

/* services */
.services{position:absolute;left:0;top:553px;width:986px;height:623px;background:var(--soft);text-align:center}
.services .eyebrow{margin-top:48px}
.services h2{font-size:34px;font-weight:700;margin-top:6px;line-height:40px}
.services .lead{font-size:14.5px;line-height:19px;color:var(--text);margin:8px auto 0;width:520px;font-weight:500}
.cards{position:absolute;left:48px;top:175px;width:890px;display:grid;grid-template-columns:repeat(3,283px);column-gap:20.5px;row-gap:16px;text-align:left}
.card{height:188px;background:var(--white);border-radius:4px;box-shadow:0 1px 6px #0000000f;padding:26px 26px 0}
.card .icon{width:54px;height:54px;border-radius:50%;background:var(--blue);display:flex;align-items:center;justify-content:center}
.card h3{font-size:17px;font-weight:700;margin-top:16px}
.card p{font-size:8.5px;line-height:13px;color:var(--text);margin-top:9px;height:28px}
.card .more{display:inline-block;font-size:9px;font-weight:700;color:var(--blue);margin-top:8px}
.card-featured{background:var(--blue);color:var(--white)}
.card-featured .icon{background:var(--white)}
.card-featured p,.card-featured .more{color:var(--white)}

/* about */
.about{position:absolute;left:0;top:1176px;width:986px;height:357px;background:var(--white)}
.about-copy{position:absolute;left:48px;top:86px;width:432px}
.about-copy h2{font-size:33px;line-height:40px;font-weight:700;margin-top:6px}
.about-copy p{font-size:8.5px;line-height:13.5px;color:var(--text);margin-top:14px}
.about-copy .btn{font-size:7.5px;padding:3px 6px;margin-top:14px}
.about-photo{position:absolute;left:508px;top:52px;width:430px;height:253px;border-radius:8px;background:linear-gradient(135deg,#c9d7e6 0%,#8fa7c1 40%,#5d7591 70%,#a9b8c7 100%)}

/* values */
.values{position:absolute;left:0;top:1533px;width:986px;height:99px;background:var(--soft);display:flex;padding:26px 48px 0}
.value{flex:1;display:flex;align-items:center;gap:9px;padding-left:0;height:48px;border-right:1px solid var(--line);margin-right:0}
.value + .value{padding-left:52px}
.value:last-child{border:none}
.value h4{font-size:14px;font-weight:700;line-height:16px}
.value span{font-size:12px;color:var(--text);font-weight:500}

/* fleet */
.fleet{position:absolute;left:0;top:1632px;width:986px;height:326px;background:var(--black)}
.fleet-photo{position:absolute;left:0;top:0;width:700px;height:326px;background:linear-gradient(180deg,#6b5a4f 0%,#b88a5a 45%,#3b342f 62%,#1d1c1c 100%)}
.fleet-fade{position:absolute;left:0;top:0;width:986px;height:326px;background:linear-gradient(90deg,transparent 0%,transparent 55%,#000 75%)}
.fleet-copy{position:absolute;right:48px;top:62px;width:400px;text-align:right;color:var(--white)}
.fleet-copy .eyebrow{color:var(--white)}
.fleet-copy h2{font-size:33px;line-height:40px;font-weight:700;margin-top:6px}
.fleet-copy p{font-size:12.5px;line-height:21px;margin-top:12px;font-weight:500}
.fleet-copy .btn{background:var(--blue);color:var(--white);font-size:12px;padding:5px 12px;margin-top:10px}

/* cta */
.cta{position:absolute;left:0;top:1958px;width:986px;height:182px;background:var(--blue);text-align:center;color:var(--white)}
.cta h2{font-size:33px;font-weight:700;margin-top:36px;line-height:40px}
.cta p{font-size:14.5px;margin-top:4px;font-weight:500}
.cta .btn{background:var(--white);color:var(--blue);border-color:var(--white);margin-top:14px;font-size:11px}

/* footer */
.footer{position:absolute;left:0;top:2140px;width:986px;height:281px;background:var(--black);color:var(--white)}
.f-brand{position:absolute;left:131px;top:46px;width:170px}
.f-brand .brand-name{font-size:17px}
.f-brand .brand-name small{font-size:17px}
.f-brand p{font-size:7.5px;line-height:12px;margin-top:14px}
.f-brand .member-badge{margin-top:16px}
.f-brand .member-badge .dot{width:30px;height:22px}
.f-brand .member-badge span{color:var(--white);font-size:21px}
.f-brand .member-badge em{color:var(--white);margin:-26px 0 0 40px;font-size:8px}
.f-div{position:absolute;top:38px;width:1px;height:168px;background:#ffffff55}
.f-col{position:absolute;top:55px}
.f-col h5{font-size:12px;font-weight:700;color:var(--blue);letter-spacing:.3px}
.f-col ul{list-style:none;margin-top:6px}
.f-col li{font-size:7.5px;line-height:18.5px}
.f-col li::before{content:"";display:inline-block;border-left:4px solid var(--blue);border-top:2.5px solid transparent;border-bottom:2.5px solid transparent;margin-right:5px}
.f-contact li::before{display:none}
.f-contact li{display:flex;gap:6px;align-items:flex-start;line-height:11px;margin-bottom:10px}
.f-contact svg{flex:none}
.f-bottom{position:absolute;left:131px;top:235px;width:724px;border-top:1px solid #ffffff44;padding-top:17px;display:flex;justify-content:space-between;font-size:7.5px}
.f-bottom nav{display:flex;gap:20px}
</style>
</head>
<body>
<div class="stage">
<div class="site">

  <header class="hero">
    <div class="hero-photo" role="img" aria-label="Private jet parked outside a hangar on a wet apron"></div>
    <svg class="hero-curve" width="986" height="553" viewBox="0 0 986 553" aria-hidden="true">
      <path d="M0 448 Q210 500 400 553 L986 553 L986 300 Q700 420 400 553 Q210 500 0 448 Z" fill="#f5f7fa"/>
      <path d="M0 448 Q210 500 400 553 L0 553 Z" fill="#f5f7fa"/>
    </svg>
    <a class="brand" href="#">
      <span class="brand-mark"></span>
      <span class="brand-name">VIRETON<small>AVIATION GROUP</small></span>
    </a>
    <nav class="nav">
      <a href="#">Home</a><a href="#">About</a><a href="#">Aircraft Management</a><a href="#">Charter</a><a href="#">Pilot Services</a><a href="#">Trip Support</a><a class="nav-contact" href="#">CONTACT</a>
    </nav>
    <div class="hero-copy">
      <div class="kicker">VIRETON AVIATION GROUP</div>
      <h1>ELEVATING AVIATION EXCELLENCE</h1>
      <p>A unified aviation group delivering world-class aircraft management, charter, acquisition, and pilot services with precision, safety, and trust.</p>
      <div class="btns">
        <a class="btn btn-solid" href="#">START A CONSULTATION</a>
        <a class="btn btn-line" href="#">EXPLORE SERVICES</a>
      </div>
      <div class="member">
        <div class="member-badge"><span class="dot"></span><em>member of</em><span>PJFO</span></div>
        <div class="line1">Built for operators, owners, and charter clients.</div>
        <div class="line2">Precision-led service architecture for every aviation business unit.</div>
      </div>
    </div>
  </header>

  <section class="services">
    <div class="eyebrow">What we do</div>
    <h2>COMPREHENSIVE AVIATION SOLUTIONS</h2>
    <p class="lead">Our integrated service offering ensures that every aspect of aviation is handled with precision, efficiency, and professionalism.</p>
    <div class="cards">
      <article class="card">
        <div class="icon"><svg width="30" height="30" viewBox="0 0 30 30" fill="none" stroke="#fff" stroke-width="1.6"><circle cx="15" cy="15" r="8"/><circle cx="15" cy="15" r="3"/><path d="M15 3v4M15 23v4M3 15h4M23 15h4M6.5 6.5l3 3M20.5 20.5l3 3M6.5 23.5l3-3M20.5 9.5l3-3"/></svg></div>
        <h3>Aircraft Management</h3>
        <p>End-to-end aircraft management solutions designed to optimize performance, ensure compliance, and deliver complete peace of mind.</p>
        <a class="more" href="#">Learn More <svg class="arrow" viewBox="0 0 26 6"><path d="M0 3h24M21 .5 24 3l-3 2.5" stroke="#0b5eb0" fill="none"/></svg></a>
      </article>
      <article class="card">
        <div class="icon"><svg width="30" height="30" viewBox="0 0 30 30" fill="none" stroke="#fff" stroke-width="1.6"><rect x="5" y="5" width="6" height="7"/><rect x="12" y="5" width="6" height="7"/><rect x="19" y="5" width="6" height="7"/><path d="M4 22c4-3 8-3 11-1h6c2 0 2 2 0 2h-6M4 26l6-1"/></svg></div>
        <h3>Aircraft Acquisition</h3>
        <p>Expert guidance through buying and selling aircraft, backed by market insight and industry experience to secure the best value.</p>
        <a class="more" href="#">View Details <svg class="arrow" viewBox="0 0 26 6"><path d="M0 3h24M21 .5 24 3l-3 2.5" stroke="#0b5eb0" fill="none"/></svg></a>
      </article>
      <article class="card">
        <div class="icon"><svg width="30" height="30" viewBox="0 0 30 30" fill="none" stroke="#fff" stroke-width="1.6"><path d="M5 17l20-8-3 6-10 3-4 5-1-4z"/><path d="M8 10l6 3"/></svg></div>
        <h3>Charter Services</h3>
        <p>On-demand charter services offering flexibility, comfort, and efficiency—tailored to your schedule and travel requirements.</p>
        <a class="more" href="#">Book a Flight <svg class="arrow" viewBox="0 0 26 6"><path d="M0 3h24M21 .5 24 3l-3 2.5" stroke="#0b5eb0" fill="none"/></svg></a>
      </article>
      <article class="card">
        <div class="icon"><svg width="30" height="30" viewBox="0 0 30 30" fill="none" stroke="#fff" stroke-width="1.6"><circle cx="15" cy="10" r="4"/><path d="M10 6h10M4 22c4-3 8-3 11-1h6c2 0 2 2 0 2h-6M4 26l6-1"/></svg></div>
        <h3>Global Trip Support</h3>
        <p>Comprehensive trip planning including permits, fuel coordination, and ground logistics to ensure seamless operations worldwide.</p>
        <a class="more" href="#">Find pilot support <svg class="arrow" viewBox="0 0 26 6"><path d="M0 3h24M21 .5 24 3l-3 2.5" stroke="#0b5eb0" fill="none"/></svg></a>
      </article>
      <article class="card">
        <div class="icon"><svg width="30" height="30" viewBox="0 0 30 30" fill="none" stroke="#fff" stroke-width="1.6"><circle cx="14" cy="16" r="9"/><circle cx="14" cy="14" r="3"/><path d="M9 22c1-3 9-3 10 0M19 4h7v5h-4l-3 2z"/></svg></div>
        <h3>Global Trip Support</h3>
        <p>Mission planning, coordination, logistics, and responsive operational support from departure to arrival.</p>
        <a class="more" href="#">Get Support <svg class="arrow" viewBox="0 0 26 6"><path d="M0 3h24M21 .5 24 3l-3 2.5" stroke="#0b5eb0" fill="none"/></svg></a>
      </article>
      <article class="card card-featured">
        <div class="icon"><svg width="30" height="30" viewBox="0 0 30 30" fill="none" stroke="#0b5eb0" stroke-width="1.6"><rect x="6" y="4" width="18" height="11"/><circle cx="9" cy="20" r="2"/><circle cx="15" cy="20" r="2"/><circle cx="21" cy="20" r="2"/><path d="M6 26h18M10 9h10"/></svg></div>
        <h3>Turbine Training Programs</h3>
        <p>Advanced pilot training programs designed to meet insurance requirements and enhance operational safety and performance.</p>
        <a class="more" href="#">Start Training <svg class="arrow" viewBox="0 0 26 6"><path d="M0 3h24M21 .5 24 3l-3 2.5" stroke="#fff" fill="none"/></svg></a>
      </article>
    </div>
  </section>

  <section class="about">
    <div class="about-copy">
      <div class="eyebrow">Who we are</div>
      <h2>A Unified Approach to Aviation Services</h2>
      <p>Vireton Aviation Group brings together multiple aviation-focused businesses under one trusted brand. We provide seamless, high-quality services across aircraft management, charter, acquisition, and training. Our team works with corporate clients, aircraft owners, and aviation professionals, delivering consistent excellence while allowing each specialized division to operate with focused expertise.</p>
      <a class="btn btn-solid" href="#">LEARN MORE <svg class="arrow" style="width:16px" viewBox="0 0 16 6"><path d="M0 3h14M11 .5 14 3l-3 2.5" stroke="#fff" fill="none"/></svg></a>
    </div>
    <div class="about-photo" role="img" aria-label="Two pilots reviewing documents beside an open-canopy aircraft"></div>
  </section>

  <section class="values">
    <div class="value">
      <svg width="36" height="38" viewBox="0 0 36 38" fill="none" stroke="#0b5eb0" stroke-width="1.5"><path d="M18 3l12 5v10c0 9-6 14-12 16C12 32 6 27 6 18V8z"/><path d="M13 18l4 4 7-8"/></svg>
      <div><h4>SAFETY</h4><span>Our Highest Standard</span></div>
    </div>
    <div class="value">
      <svg width="36" height="38" viewBox="0 0 36 38" fill="none" stroke="#0b5eb0" stroke-width="1.5"><circle cx="18" cy="19" r="9"/><path d="M9 19h18M18 10c-4 5-4 13 0 18M18 10c4 5 4 13 0 18"/><circle cx="18" cy="4" r="2"/><circle cx="18" cy="34" r="2"/><circle cx="3" cy="19" r="2"/><circle cx="33" cy="19" r="2"/></svg>
      <div><h4>GLOBAL REACH</h4><span>Worldwide Solutions</span></div>
    </div>
    <div class="value">
      <svg width="36" height="38" viewBox="0 0 36 38" fill="none" stroke="#0b5eb0" stroke-width="1.5"><path d="M3 10V4h6M27 4h6v6M3 28v6h6M27 34h6v-6"/><circle cx="18" cy="19" r="9"/><circle cx="18" cy="16" r="3"/><path d="M12 25c2-4 10-4 12 0"/></svg>
      <div><h4>CLIENT FOCUSED</h4><span>Personalized Service</span></div>
    </div>
    <div class="value">
      <svg width="36" height="38" viewBox="0 0 36 38" fill="none" stroke="#0b5eb0" stroke-width="1.5"><circle cx="18" cy="18" r="12"/><circle cx="18" cy="18" r="6"/><path d="M13 30l-2 6M23 30l2 6"/></svg>
      <div><h4>EXCELLENCE</h4><span>In Every Detail</span></div>
    </div>
  </section>

  <section class="fleet">
    <div class="fleet-photo" role="img" aria-label="Business jet on the apron at sunset"></div>
    <div class="fleet-fade"></div>
    <div class="fleet-copy">
      <div class="eyebrow">Our fleet</div>
      <h2>Access the Right Aircraft for Every Mission</h2>
      <p>From light jets to long-range aircraft, we provide access to a diverse fleet that meets the highest standards of performance, comfort and reliability.</p>
      <a class="btn" href="#">View Aircraft Options <svg class="arrow" style="width:22px" viewBox="0 0 22 6"><path d="M0 3h20M17 .5 20 3l-3 2.5" stroke="#fff" fill="none"/></svg></a>
    </div>
  </section>

  <section class="cta">
    <h2>Ready to Elevate Your Aviation Experience?</h2>
    <p>Contact our team today to discuss how we can support your aviation needs.</p>
    <a class="btn" href="#">GET IN TOUCH <svg class="arrow" style="width:22px" viewBox="0 0 22 6"><path d="M0 3h20M17 .5 20 3l-3 2.5" stroke="#0b5eb0" fill="none"/></svg></a>
  </section>

  <footer class="footer">
    <div class="f-brand">
      <div class="brand-name">VIRETON<small>AVIATION GROUP</small></div>
      <p>Delivering world-class aviation solutions through a family of trusted companies committed to safety, service, and sophistication.</p>
      <div class="member-badge"><span class="dot"></span><em>member of</em><span>PJFO</span></div>
    </div>
    <div class="f-div" style="left:347px"></div>
    <div class="f-col" style="left:394px">
      <h5>QUICK LINKS</h5>
      <ul><li>About</li><li>Aircraft Management</li><li>Aircraft Acquisition</li><li>Charter</li><li>Pilot Services</li><li>Trip Support</li><li>Contact</li></ul>
    </div>
    <div class="f-col" style="left:543px">
      <h5>SERVICES</h5>
      <ul><li>Aircraft Management</li><li>Aircraft Acquisition</li><li>Charter</li><li>Pilot Services</li><li>Trip Support</li></ul>
    </div>
    <div class="f-div" style="left:677px"></div>
    <div class="f-col f-contact" style="left:724px">
      <h5>CONTACT INFO</h5>
      <ul style="margin-top:12px">
        <li><svg width="12" height="12" viewBox="0 0 12 12" fill="none" stroke="#0b5eb0"><rect x="3" y="1" width="6" height="10" rx="1"/></svg>+1 (305) 555-0142</li>
        <li><svg width="12" height="12" viewBox="0 0 12 12" fill="none" stroke="#0b5eb0"><rect x="1" y="3" width="10" height="7"/><path d="M1 3l5 4 5-4"/></svg>info@viretonaviation.com</li>
        <li><svg width="12" height="12" viewBox="0 0 12 12" fill="none" stroke="#0b5eb0"><path d="M6 11S2 7 2 4.5a4 4 0 0 1 8 0C10 7 6 11 6 11z"/><circle cx="6" cy="4.5" r="1.3"/></svg>480 Skyline Way, Suite 100<br>Miami, FL 33101, USA</li>
        <li><svg width="12" height="12" viewBox="0 0 12 12" fill="none" stroke="#0b5eb0"><rect x="1" y="2" width="10" height="9"/><path d="M1 5h10"/></svg>24/7 Support Available</li>
      </ul>
    </div>
    <div class="f-bottom">
      <span>© 2024 Vireton Aviation Group. All rights reserved.</span>
      <nav><a href="#">Privacy Policy</a><a href="#">Terms of Service</a></nav>
    </div>
  </footer>

</div>
</div>
</body>
</html>
```